Private Investigation Business Card Design

I need a business card for a new private investigation company named Brisk Inquiries. I perform mainly surveillance jobs, vehicle repossessions, document serves etc. The final design should aim for a professional look. The logo has a magnifying glass with stick man arms and legs and is in a running action to show the "Brisk" aspect of the name. If the colour scheme could remain the same as the website www.briskinquiries-demo.com.au with silvers,blacks and a couple electric blue highlights.
Industry/Entity Type
Business
Contact Information for Business Card
Morgan Kellaway
Brisk Inquiries
0487316204
PO Box 58, Carnwell NSW 2291
info@briskinquiries-demo.com.au
www.briskinquiries-demo.com.au
Look and feel

```html
<!DOCTYPE html>
<html lang="en">
<head>
<meta charset="utf-8">
<title>Brisk Inquiries – Business Card</title>
<link rel="stylesheet" href="https://fonts.googleapis.com/css2?family=Saira:wght@400;600&family=Open+Sans:ital,wght@1,400&display=swap">
<style>
  :root {
    --backdrop: #3b3b3b;
    --card-white: #fbfbfb;
    --ink: #1d1d1d;
    --ink-soft: #4a4a4a;
    --rule: #c9c9c9;
    --silver-light: #dcdcdc;
    --silver-dark: #8e8e8e;
    --band-black: #1a1a1a;
  }
  * { margin: 0; padding: 0; box-sizing: border-box; }
  html, body {
    width: 1200px; height: 750px; overflow: hidden;
    background: var(--backdrop);
  }
  .card {
    position: absolute;
    left: 371px;
    width: 461px;
    height: 263px;
    overflow: hidden;
  }
  .card--front { top: 101px; background: var(--card-white); }
  .card--back {
    top: 401px;
    background: radial-gradient(ellipse at 50% 45%, var(--silver-light) 0%, #b9b9b9 55%, var(--silver-dark) 100%);
  }

  .brand {
    position: absolute; left: 30px; top: 30px;
    display: flex; align-items: center; gap: 8px;
    font-family: "Saira", sans-serif; font-weight: 600;
    font-size: 26px; color: var(--ink); letter-spacing: 0.5px;
  }
  .brand__dot {
    width: 14px; height: 14px; border-radius: 50%;
    background: var(--ink);
  }

  .holder {
    position: absolute; right: 34px; top: 133px;
    font-family: "Saira", sans-serif; font-weight: 600;
    font-size: 16px; color: var(--ink);
  }
  .divider {
    position: absolute; left: 30px; top: 165px;
    width: 393px; height: 1px; background: var(--rule);
  }

  .contacts {
    position: absolute; left: 30px; top: 179px;
    list-style: none;
    font-family: "Saira", sans-serif; font-weight: 400;
    color: var(--ink-soft);
  }
  .contacts li {
    display: flex; align-items: center; gap: 7px;
    height: 18px; font-size: 10.5px;
  }
  .contacts li.contacts__phone { font-size: 12px; }
  .contacts svg { width: 11px; height: 11px; fill: var(--ink); flex: none; }

  .address {
    position: absolute; right: 32px; top: 200px;
    text-align: right;
    font-family: "Saira", sans-serif; font-size: 11px;
    line-height: 14.5px; color: var(--ink-soft);
  }

  .band { position: absolute; left: 0; bottom: 0; width: 461px; height: 11px; }

  .back-brand {
    position: absolute; left: 0; right: 0; top: 90px;
    display: flex; justify-content: center; align-items: center; gap: 12px;
    font-family: "Saira", sans-serif; font-weight: 600;
    font-size: 34px; color: var(--ink);
  }
  .back-brand__dot {
    width: 22px; height: 22px; border-radius: 50%; background: var(--ink);
  }
  .back-url {
    position: absolute; left: 0; right: 0; top: 211px;
    text-align: center;
    font-family: "Open Sans", sans-serif; font-style: italic;
    font-size: 11px; letter-spacing: 3.6px; color: #3a3a3a;
  }
</style>
</head>
<body>
  <section class="card card--front" aria-label="Business card front">
    <div class="brand"><span class="brand__dot"></span>Brisk Inquiries</div>

    <p class="holder">Morgan Kellaway</p>
    <div class="divider"></div>

    <ul class="contacts">
      <li class="contacts__phone">
        <svg viewBox="0 0 24 24" aria-hidden="true"><path d="M6.6 10.8a15.1 15.1 0 0 0 6.6 6.6l2.2-2.2a1 1 0 0 1 1-.25 11.4 11.4 0 0 0 3.6.57 1 1 0 0 1 1 1V20a1 1 0 0 1-1 1A17 17 0 0 1 3 4a1 1 0 0 1 1-1h3.5a1 1 0 0 1 1 1c0 1.25.2 2.45.57 3.57a1 1 0 0 1-.25 1z"/></svg>
        0487 316 204
      </li>
      <li>
        <svg viewBox="0 0 24 24" aria-hidden="true"><path d="M2 5h20v14H2zm2 2v.5l8 5 8-5V7zm0 2.8V17h16V9.8l-8 5z"/></svg>
        info@briskinquiries-demo.com.au
      </li>
      <li>
        <svg viewBox="0 0 24 24" aria-hidden="true"><circle cx="12" cy="12" r="10"/><path d="M7 6c2 1 3 3 2 5s1 3 2 5M15 4c-1 2 0 3 2 4s2 4 1 6" stroke="#fbfbfb" stroke-width="2" fill="none"/></svg>
        www.briskinquiries-demo.com.au
      </li>
    </ul>

    <p class="address">PO Box 58<br>Carnwell NSW 2291</p>

    <svg class="band" viewBox="0 0 461 11" preserveAspectRatio="none" aria-hidden="true">
      <defs>
        <linearGradient id="bandSilver" x1="0" x2="1" y1="0" y2="0">
          <stop offset="0" stop-color="#8a8a8a"/>
          <stop offset="1" stop-color="#d2d2d2"/>
        </linearGradient>
      </defs>
      <polygon points="0,0 300,0 297,11 0,11" fill="url(#bandSilver)"/>
      <polygon points="304,0 461,0 461,11 301,11" fill="var(--band-black)"/>
    </svg>
  </section>

  <section class="card card--back" aria-label="Business card back">
    <div class="back-brand"><span class="back-brand__dot"></span>Brisk Inquiries</div>
    <p class="back-url">www.briskinquiries-demo.com.au</p>
  </section>
</body>
</html>
```